Need to drive pregnant women to my 3d4d ultrasound studio where i provide 4d ultrasound with hyperalistic imaging and gender reveals

Industry/Entity Type

Healthcare

Font styles to use
Decorative
Script

Requirements
Must have
• My Company name Cielo de Nuestra Espera 4D. EVERYTHING HAS TO BE IN SPANISH
Nice to have
• SIMPLE AND NOT TOO BUSY
Should not have
• website

```html
<!DOCTYPE html>
<html lang="es">
<head>
<meta charset="utf-8">
<title>Cielo de Nuestra Espera 4D</title>
<link rel="stylesheet" href="https://fonts.googleapis.com/css2?family=Montserrat:wght@300;500;600;700;800&family=Gochi+Hand&display=swap">
<style>
  :root {
    --backdrop: #666666;
    --plum-deep: #3d2160;
    --plum-mid: #6f4c9f;
    --lavender: #c7a6e8;
    --blush: #e6c9e3;
    --blush-band: #dcc0df;
    --ink: #3a2151;
    --pink-accent: #ecc7e0;
    --white: #ffffff;
    --heart-red: #e0242c;
    --ultrasound: #b8682a;
    --skin: #e8c2ac;
    --dress: #8fd1c8;
  }
  html, body {
    margin: 0;
    width: 1200px;
    height: 748px;
    overflow: hidden;
    background: var(--backdrop);
    font-family: "Montserrat", sans-serif;
  }
  .banner {
    position: absolute;
    left: 98px;
    top: 123px;
    width: 1003px;
    height: 501px;
    overflow: hidden;
    box-shadow: 6px 8px 14px rgba(0,0,0,.35);
  }
  .banner-bg { position: absolute; inset: 0; }
  .brand-badge {
    position: absolute;
    left: 193px; top: 27px;
    width: 108px; height: 108px;
    border-radius: 50%;
    background: var(--white);
    display: flex; align-items: center; justify-content: center;
    text-align: center;
    font-size: 11px; font-weight: 700;
    color: var(--plum-mid);
    line-height: 1.25;
    padding: 12px; box-sizing: border-box;
  }
  .headline { position: absolute; left: 40px; width: 390px; text-align: center; color: var(--white); margin: 0; }
  .headline-intro { top: 148px; font-size: 29px; font-weight: 300; letter-spacing: 3px; }
  .headline-main { top: 178px; font-size: 76px; font-weight: 800; letter-spacing: -1px; line-height: 1; }
  .headline-sub { top: 256px; font-size: 52px; font-weight: 800; color: var(--pink-accent); line-height: 1; }
  .services {
    position: absolute; left: 5px; width: 460px; top: 317px; margin: 0;
    text-align: center; color: var(--white);
    font-size: 16px; font-weight: 600; line-height: 26px;
  }
  .amp {
    display: inline-block; width: 20px; height: 20px; border-radius: 50%;
    background: var(--pink-accent); color: var(--ink);
    font-size: 12px; line-height: 20px; margin-left: 4px; vertical-align: 1px;
  }
  .booking-pill {
    position: absolute; left: 48px; top: 400px;
    width: 361px; height: 62px;
    background: var(--white); border-radius: 31px;
    box-shadow: 0 3px 6px rgba(0,0,0,.2);
    display: flex; flex-direction: column; justify-content: center;
    padding-left: 30px; box-sizing: border-box;
    color: var(--ink);
  }
  .booking-title { font-size: 22px; font-weight: 800; line-height: 1.05; }
  .booking-note { font-size: 13px; font-weight: 700; }
  .contact-phone {
    position: absolute; left: 438px; top: 408px;
    display: flex; align-items: center; gap: 4px;
    font-size: 31px; font-weight: 600; color: var(--ink);
  }
  .contact-social {
    position: absolute; left: 442px; top: 444px;
    display: flex; align-items: center; gap: 10px;
    font-size: 16px; font-weight: 600; color: var(--ink);
  }
  .social-dot { width: 18px; height: 18px; border-radius: 50%; background: #4a63b8; }
  .snapshot {
    position: absolute; background: var(--white); padding: 10px;
    box-sizing: border-box; box-shadow: 2px 4px 8px rgba(0,0,0,.3);
  }
  .snapshot-inner { width: 100%; height: 100%; }
  .snapshot-scan { left: 456px; top: 33px; width: 184px; height: 220px; transform: rotate(-3deg); padding-bottom: 22px; }
  .snapshot-scan .snapshot-inner { background: radial-gradient(circle at 45% 45%, #d99552, var(--ultrasound) 55%, #3a1d0a); }
  .snapshot-newborn { left: 593px; top: 170px; width: 190px; height: 212px; transform: rotate(2deg); padding-bottom: 14px; z-index: 2; }
  .snapshot-newborn .snapshot-inner { background: radial-gradient(circle at 50% 55%, #f2d3c2, var(--skin) 60%, #b98a72); }
  .tagline {
    position: absolute; left: 648px; top: 58px; width: 140px; margin: 0;
    font-family: "Gochi Hand", cursive; font-size: 28px; line-height: 31px;
    color: var(--white); text-align: center;
    z-index: 3;
  }
  .model-photo {
    position: absolute; left: 790px; top: 21px; width: 213px; height: 480px;
    background: linear-gradient(180deg, #5a3a2c 0%, var(--skin) 28%, var(--dress) 45%, #7fc5bc 100%);
    border-radius: 100px 70px 0 0;
    opacity: .95;
    z-index: 1;
  }
  .heart-badge {
    position: absolute; background: var(--heart-red); border-radius: 22%;
    box-shadow: 0 3px 6px rgba(0,0,0,.3);
    display: flex; align-items: center; justify-content: center;
    z-index: 4;
  }
  .heart-badge svg { width: 58%; height: 58%; }
  .heart-blur { filter: blur(2px); }
</style>
</head>
<body>
  <section class="banner">
    <svg class="banner-bg" viewBox="0 0 1003 501" preserveAspectRatio="none" aria-hidden="true">
      <defs>
        <linearGradient id="purple-sweep" x1="0" y1="1" x2="1" y2="0">
          <stop offset="0" stop-color="#3a1f5a"/>
          <stop offset=".4" stop-color="#5d3a8c"/>
          <stop offset=".75" stop-color="#9a74cc"/>
          <stop offset="1" stop-color="#d3b4ef"/>
        </linearGradient>
      </defs>
      <rect width="1003" height="501" fill="url(#purple-sweep)"/>
      <path d="M0,0 H290 C250,90 150,118 70,110 C35,106 12,100 0,92 Z" fill="var(--blush)"/>
      <path d="M0,420 C150,470 300,392 480,378 C620,368 720,382 790,360 L1003,340 V501 H0 Z" fill="var(--blush-band)"/>
    </svg>

    <div class="brand-badge">Cielo de Nuestra Espera 4D</div>

    <p class="headline headline-intro">Descubre el</p>
    <h1 class="headline headline-main">Milagro</h1>
    <p class="headline headline-sub">de la Vida</p>

    <p class="services">Ultrasonido 4D <span class="amp">&amp;</span><br>Revelación de Género e Imágenes Hiperrealistas</p>

    <div class="snapshot snapshot-scan"><div class="snapshot-inner" role="img" aria-label="Imagen de ultrasonido 4D de un bebé"></div></div>
    <div class="snapshot snapshot-newborn"><div class="snapshot-inner" role="img" aria-label="Fotografía de un recién nacido dormido"></div></div>

    <p class="tagline">Recuerdos<br>Para Toda<br>la Vida</p>

    <div class="model-photo" role="img" aria-label="Mujer embarazada con vestido turquesa sosteniendo su vientre"></div>

    <div class="booking-pill">
      <span class="booking-title">RESERVA TU SESIÓN EN</span>
      <span class="booking-note">Nuestro Estudio de Ultrasonido 3D/4D Hoy</span>
    </div>

    <div class="contact-phone">
      <svg width="30" height="30" viewBox="0 0 30 30" aria-hidden="true">
        <circle cx="15" cy="15" r="14" fill="var(--ink)"/>
        <path d="M10.5 8.5 l3 3 -1.6 1.8 c1 2 2.6 3.6 4.6 4.6 l1.8 -1.6 3 3 -2 2 c-5 -.5 -10.3 -5.8 -10.8 -10.8 z" fill="var(--white)"/>
      </svg>
      <span>+1 555-014-2738</span>
    </div>
    <div class="contact-social">
      <span class="social-dot"></span>
      <span>@Cielo-de-Nuestra-Espera-4D</span>
    </div>

    <div class="heart-badge heart-blur" style="left:66px;top:-14px;width:56px;height:44px"><svg viewBox="0 0 24 22"><path d="M12 21 C5 15 1 11 1 6.5 A5.5 5.5 0 0 1 12 4 A5.5 5.5 0 0 1 23 6.5 C23 11 19 15 12 21Z" fill="#fff"/></svg></div>
    <div class="heart-badge" style="left:364px;top:146px;width:28px;height:28px;transform:rotate(-12deg)"><svg viewBox="0 0 24 22"><path d="M12 21 C5 15 1 11 1 6.5 A5.5 5.5 0 0 1 12 4 A5.5 5.5 0 0 1 23 6.5 C23 11 19 15 12 21Z" fill="#fff"/></svg></div>
    <div class="heart-badge" style="left:482px;top:250px;width:78px;height:70px;transform:rotate(-8deg)"><svg viewBox="0 0 24 22"><path d="M12 21 C5 15 1 11 1 6.5 A5.5 5.5 0 0 1 12 4 A5.5 5.5 0 0 1 23 6.5 C23 11 19 15 12 21Z" fill="#fff"/></svg></div>
    <div class="heart-badge" style="left:28px;top:388px;width:38px;height:36px;transform:rotate(-12deg)"><svg viewBox="0 0 24 22"><path d="M12 21 C5 15 1 11 1 6.5 A5.5 5.5 0 0 1 12 4 A5.5 5.5 0 0 1 23 6.5 C23 11 19 15 12 21Z" fill="#fff"/></svg></div>
    <div class="heart-badge heart-blur" style="left:948px;top:382px;width:64px;height:64px;transform:rotate(10deg)"><svg viewBox="0 0 24 22"><path d="M12 21 C5 15 1 11 1 6.5 A5.5 5.5 0 0 1 12 4 A5.5 5.5 0 0 1 23 6.5 C23 11 19 15 12 21Z" fill="#fff"/></svg></div>
  </section>
</body>
</html>
```